Card Design for my dog training business Brightpaw Obedience

Need a business card design for my dog training business with my new logo. Want the card to come off professional yet fun. Want it to be very eye catchy as well. I normally have these at vet clinics, pet stores, and groomers. so need it to look better than my competitors.
Target Market(s)
dog owners
Industry/Entity Type
Dog Training
Contact Information for Business Card
needs logo, my name and info
Font styles to use
Serif
Colors
0255a3
ffffff
ec1f27
000000
333333
fbfbfb
Requirements
Must have
- Brightpaw Obedience
- Felix Orland
- 415 903 2276
- info@brightpawobedience.example
- www.brightpawobedience.example

```html
<!DOCTYPE html>
<html lang="en">
<head>
<meta charset="utf-8">
<title>Brightpaw Obedience – Business Card</title>
<link rel="stylesheet" href="https://fonts.googleapis.com/css2?family=EB+Garamond:ital,wght@0,400;1,400&family=Montserrat:wght@400;500&display=swap">
<style>
  :root {
    --blue: #0255a3;
    --red: #ec1f27;
    --white: #ffffff;
    --paper: #fbfbfb;
    --ink: #333333;
    --black: #000000;
    --card-dark: #1f2124;
    --silver: #d9d9d9;
    --backdrop: #e6e3de;
  }
  * { margin: 0; padding: 0; box-sizing: border-box; }
  html, body { width: 1200px; height: 866px; overflow: hidden; }
  body {
    background: var(--backdrop);
    position: relative;
    font-family: "Montserrat", Arial, sans-serif;
  }
  .card {
    position: absolute;
    width: 560px;
    height: 320px;
    border-radius: 4px;
    overflow: hidden;
    box-shadow: 0 10px 28px rgba(0,0,0,0.18);
  }

  /* Front card */
  .card--front {
    left: 50px; top: 90px;
    background: linear-gradient(160deg, #2a2c30 0%, var(--card-dark) 60%, #17181a 100%);
    color: var(--silver);
  }
  .brand {
    position: absolute;
    left: 0; right: 0; top: 108px;
    text-align: center;
    font-family: "EB Garamond", Georgia, serif;
    font-size: 40px;
    font-weight: 400;
    letter-spacing: 1px;
    color: var(--silver);
  }
  .tagline {
    position: absolute;
    left: 0; right: 0; bottom: 46px;
    text-align: center;
    font-family: "EB Garamond", Georgia, serif;
    font-style: italic;
    font-size: 24px;
    color: var(--white);
  }

  /* Back card */
  .card--back {
    left: 590px; top: 456px;
    background: var(--paper);
  }
  .card-art {
    position: absolute;
    left: 0; top: 0;
    width: 560px; height: 320px;
  }
  .holder-name {
    position: absolute;
    left: 150px; top: 58px;
    font-size: 21px;
    font-weight: 500;
    letter-spacing: 1.5px;
    color: var(--blue);
    text-transform: uppercase;
  }
  .contact-list {
    position: absolute;
    right: 22px; top: 150px;
    list-style: none;
    text-align: right;
    color: var(--ink);
    font-size: 12px;
    line-height: 24px;
  }
  .contact-list li { display: flex; justify-content: flex-end; align-items: center; gap: 8px; }
  .contact-icon { width: 13px; height: 13px; flex: none; }
</style>
</head>
<body>

  <section class="card card--front" aria-label="Card front">
    <div class="brand">Brightpaw Obedience</div>
    <p class="tagline">“Training dogs across Texas one dog at a time.”</p>
  </section>

  <section class="card card--back" aria-label="Card back">
    <svg class="card-art" viewBox="0 0 560 320">
      <defs>
        <linearGradient id="dogTones" x1="0" y1="0" x2="1" y2="0">
          <stop offset="0" stop-color="#0255a3"/>
          <stop offset="0.55" stop-color="#5a6fb0"/>
          <stop offset="1" stop-color="#ec1f27"/>
        </linearGradient>
      </defs>
      <polygon points="0,110 110,70 140,320 0,320" fill="#1f2124"/>
      <rect role="img" aria-label="Illustration of two dog heads in blue and red line art" x="20" y="100" width="250" height="220" fill="url(#dogTones)" opacity="0.85"/>
    </svg>

    <h1 class="holder-name">Felix Orland</h1>

    <ul class="contact-list">
      <li>415 903 2276
        <svg class="contact-icon" viewBox="0 0 16 16"><path d="M4 1.5 6.5 4 5 6c.8 1.8 2.2 3.2 4 4l2-1.5 2.5 2.5-1.5 2.5C7 13.5 2.5 9 1.5 3z" fill="#0255a3"/></svg>
      </li>
      <li>info@brightpawobedience.example
        <svg class="contact-icon" viewBox="0 0 16 16"><rect x="1" y="3" width="14" height="10" fill="#0255a3"/><path d="M1 3l7 6 7-6" fill="none" stroke="#fff" stroke-width="1.3"/></svg>
      </li>
      <li>www.brightpawobedience.example
        <svg class="contact-icon" viewBox="0 0 16 16"><circle cx="8" cy="8" r="7" fill="#0255a3"/><path d="M1 8h14M8 1c-3 3.5-3 10.5 0 14M8 1c3 3.5 3 10.5 0 14" fill="none" stroke="#fff" stroke-width="1"/></svg>
      </li>
    </ul>
  </section>

</body>
</html>
```